Law Offices business card

Hi there, I'll need business card for the Law Offices of Colin Matheny. The information must convey his strategic approach and quick resolution to complex business litigation needs. Please emphasize Civil Litigation, Corporate Law, Business Governance and Real Estate Law. Colin has over 25 years of experience in these fields.The card should be modern and edgy and the message should be clear. Please consult his current website for ideas.

```html
<!DOCTYPE html>
<html lang="en">
<head>
<meta charset="utf-8">
<title>Law Offices of Colin Matheny – Business Card</title>
<link href="https://fonts.googleapis.com/css2?family=Open+Sans:wght@400;600;700&display=swap" rel="stylesheet">
<style>
  :root {
    --stage: #3b3b3d;
    --card-light: #ffffff;
    --card-dark: #1f1f20;
    --ink: #1c1c1c;
    --ink-soft: #3a3a3a;
    --accent: #e1262c;
    --pale: #c8c6d6;
    --rule-light: #8a8a8a;
    --rule-dark: #6e6e74;
  }
  * { box-sizing: border-box; margin: 0; padding: 0; }
  html, body {
    width: 1200px; height: 900px; overflow: hidden;
    background: var(--stage);
    font-family: "Open Sans", Arial, sans-serif;
  }
  .card {
    position: absolute; left: 300px; width: 600px; height: 343px;
    border-radius: 20px; overflow: hidden;
  }
  .card--front { top: 62px; background: var(--card-light); color: var(--ink); }
  .card--back { top: 478px; background: var(--card-dark); color: var(--pale); }

  .firm-mark { position: absolute; display: flex; align-items: flex-end; gap: 10px; }
  .firm-mark__square { width: 14px; height: 14px; background: var(--accent); margin-bottom: 8px; }
  .firm-mark__name { font-weight: 600; line-height: 1; }
  .firm-mark__name small {
    display: block; font-size: 13px; letter-spacing: 2px; text-transform: uppercase; margin-bottom: 4px;
  }
  .firm-mark__name span { display: block; font-size: 36px; }

  .card--front .firm-mark { left: 120px; top: 92px; }
  .card--front .firm-mark__name { color: var(--ink); }

  .rule { position: absolute; height: 1px; }
  .card--front .rule { background: var(--rule-light); }
  .card--back .rule { background: var(--rule-dark); }
  .rule--logo { left: 400px; right: 0; top: 178px; }
  .rule--base { left: 0; right: 0; top: 300px; }

  .services {
    position: absolute; left: 0; right: 0; top: 206px; text-align: center;
    font-size: 12px; line-height: 18px; letter-spacing: 0.6px; color: var(--ink-soft);
  }
  .services .highlight { color: var(--accent); }

  .card--back .firm-mark { left: 34px; top: 30px; }
  .card--back .firm-mark__name { color: var(--pale); }
  .card--back .firm-mark__name span { font-size: 30px; }

  .holder { position: absolute; left: 44px; top: 162px; }
  .holder__name { font-size: 21px; font-weight: 700; letter-spacing: 0.3px; color: var(--pale); line-height: 26px; }
  .holder__title { font-size: 12px; letter-spacing: 1px; color: var(--accent); line-height: 16px; }
  .rule--name { left: 130px; right: 30px; top: 197px; }

  .contacts {
    position: absolute; right: 30px; top: 214px; list-style: none;
    font-size: 13px; line-height: 20px; text-align: right; color: var(--pale);
  }
  .contacts li { display: flex; justify-content: flex-end; align-items: center; gap: 8px; }
  .contacts svg { width: 11px; height: 11px; fill: var(--accent); }

  .address {
    position: absolute; left: 44px; top: 250px;
    font-size: 13px; line-height: 19px; letter-spacing: 0.3px; color: var(--pale);
  }
</style>
</head>
<body>

<section class="card card--front" aria-label="Business card front">
  <div class="firm-mark">
    <div class="firm-mark__square"></div>
    <div class="firm-mark__name"><small>Law Offices of</small><span>Colin</span><span>Matheny, PA</span></div>
  </div>
  <div class="rule rule--logo"></div>
  <p class="services">
    CIVIL LITIGATION · CORPORATE LAW<br>
    <span class="highlight">REAL ESTATE LAW</span><br>
    BUSINESS GOVERNANCE · 25+ YEARS OF EXPERIENCE
  </p>
  <div class="rule rule--base"></div>
</section>

<section class="card card--back" aria-label="Business card back">
  <div class="firm-mark">
    <div class="firm-mark__square"></div>
    <div class="firm-mark__name"><small>Law Offices of</small><span>Colin</span><span>Matheny, PA</span></div>
  </div>

  <div class="holder">
    <p class="holder__name">COLIN MATHENY</p>
    <p class="holder__title">ATTORNEY</p>
  </div>
  <div class="rule rule--name"></div>

  <ul class="contacts">
    <li>561-555-0142
      <svg viewBox="0 0 24 24"><path d="M6.6 10.8a15.1 15.1 0 0 0 6.6 6.6l2.2-2.2a1 1 0 0 1 1-.25 11.4 11.4 0 0 0 3.6.6 1 1 0 0 1 1 1V20a1 1 0 0 1-1 1A17 17 0 0 1 3 4a1 1 0 0 1 1-1h3.5a1 1 0 0 1 1 1c0 1.250.2 2.45.6 3.6a1 1 0 0 1-.25 1z"/></svg></li>
    <li>561-555-0187
      <svg viewBox="0 0 24 24"><path d="M6 2h10v6H6zM3 9h18a1 1 0 0 1 1 1v8h-4v4H6v-4H2v-8a1 1 0 0 1 1-1zm5 8v3h8v-3z"/></svg></li>
    <li>colin@mathenylaw.com
      <svg viewBox="0 0 24 24"><path d="M2 5h20v14H2zm2 2v.5l8 5 8-5V7zm0 3v7h16v-7l-8 5z"/></svg></li>
    <li>www.mathenylaw.com
      <svg viewBox="0 0 24 24"><path d="M12 2a10 10 0 1 0 0 20 10 10 0 0 0 0-20zm6.9 9h-3a15 15 0 0 0-1.3-5.5A8 8 0 0 1 18.9 11zM12 4.1c.9 1.2 1.8 3.5 1.9 6.9h-3.8c.1-3.4 1-5.7 1.9-6.9zM9.4 5.5A15 15 0 0 0 8.1 11h-3a8 8 0 0 1 4.3-5.5zM5.1 13h3a15 15 0 0 0 1.3 5.5A8 8 0 0 1 5.1 13zm6.9 6.9c-.9-1.2-1.8-3.5-1.9-6.9h3.8c-.1 3.4-1 5.7-1.9 6.9zm2.6-1.4a15 15 0 0 0 1.3-5.5h3a8 8 0 0 1-4.3 5.5z"/></svg></li>
  </ul>

  <p class="address">318B Coral Lane<br>Lake Haven, FL 33412</p>
</section>

</body>
</html>
```